RTavenor Business Cards & Letterhead

I have a logo but need a design for some new business cards. We are a Design-Build Firm that specializes in the design and construction of commercial projects.
the cards need to be professional. no cartoon stuff.
i would like to have the cards in AI format so I can update the card as needed. Logo is provided.
Our Address is: 4187 Marlowe Ct. Apex, North Carolina 27614

```html
<!DOCTYPE html>
<html lang="en">
<head>
<meta charset="utf-8">
<title>RTavenor Letterhead</title>
<link rel="stylesheet" href="https://fonts.googleapis.com/css2?family=Figtree:wght@400;600;700;800&display=swap">
<style>
  :root {
    --backdrop: #474747;
    --paper: #ffffff;
    --ink: #4a4a4a;
    --ink-dark: #3f3f40;
    --brand-blue: #0e6cad;
    --brand-blue-light: #1a8ad0;
    --brand-blue-deep: #0a4f86;
    --footer: #2b2b2b;
    --footer-text: #f2f2f2;
  }
  * { margin: 0; padding: 0; box-sizing: border-box; }
  html, body {
    width: 1200px; height: 1200px; overflow: hidden;
    background: var(--backdrop);
    font-family: "Figtree", sans-serif;
  }
  .letterhead {
    position: absolute; left: 181px; top: 30px;
    width: 838px; height: 1140px;
    background: var(--paper);
    box-shadow: 0 10px 30px rgba(0,0,0,.35);
  }
  .brand {
    position: absolute; top: 56px; left: 0; width: 100%;
    display: flex; justify-content: center; align-items: center; gap: 12px;
  }
  .brand-mark {
    width: 40px; height: 40px; background: var(--brand-blue);
  }
  .brand-name {
    font-weight: 800; font-size: 60px; line-height: 1;
    color: var(--ink-dark); letter-spacing: -0.5px;
  }
  .salutation {
    position: absolute; left: 56px; top: 237px;
    font-size: 23px; font-weight: 600; color: var(--brand-blue);
  }
  .body-copy {
    position: absolute; left: 58px; width: 720px;
    font-size: 19.3px; line-height: 27.6px; color: var(--ink);
    text-align: justify;
  }
  .body-copy.first { top: 288px; }
  .body-copy.second { top: 508px; }
  .sign-off {
    position: absolute; left: 63px; top: 882px; color: var(--ink);
  }
  .sign-off .name { font-size: 12px; line-height: 15px; }
  .sign-off .role { font-size: 10px; line-height: 14px; color: #333; }
  .signature {
    position: absolute; left: 55px; top: 916px; width: 184px; height: 82px;
    background: linear-gradient(120deg, #f4f4f4, #e4e4e4 60%, #f6f6f6);
    border-radius: 4px;
  }
  .rule {
    position: absolute; left: 0; top: 1024px; width: 100%; height: 9px;
    background: linear-gradient(90deg, var(--brand-blue-deep), var(--brand-blue-light) 50%, var(--brand-blue-deep));
  }
  .contact-bar {
    position: absolute; left: 0; top: 1043px; width: 100%; height: 97px;
    background: var(--footer); color: var(--footer-text);
    font-size: 24px; line-height: 29px;
  }
  .contact-item {
    position: absolute; display: flex; align-items: center; gap: 8px;
  }
  .contact-item svg { fill: var(--brand-blue-light); flex: none; }
  .phone { left: 122px; top: 20px; }
  .email { left: 122px; top: 49px; }
  .address { left: 425px; top: 20px; gap: 12px; }
</style>
</head>
<body>
<main class="letterhead">
  <header class="brand">
    <span class="brand-mark"></span>
    <span class="brand-name">RTavenor</span>
  </header>

  <p class="salutation">Dear Mr. John,</p>

  <p class="body-copy first">Lorem ipsum dolor sit amet, consectetuer adipiscing elit, sed diam nonummy nibh euismod tincidunt ut laoreet dolore magna aliquam erat volutpat. Ut wisi enim ad minim veniam, quis nostrud exerci tation ullamcorper suscipit lobortis nisl ut aliquip ex ea commodo consequat. Duis autem vel eum iriure dolor in hendrerit in vulputate velit esse molestie consequat, vel illum dolore eu feugiat nulla facilisis at vero eros et accumsan et iusto odio dignissim qui blandit praesent luptatum zzril delenit augue duis dolore te feugait nulla facilisi.</p>

  <p class="body-copy second">Lorem ipsum dolor sit amet, cons ectetuer adipiscing elit, sed diam nonummy nibh euismod tincidunt ut laoreet dolore magna aliquam erat volutpat. Ut wisi Lorem ipsum dolor sit amet, consectetuer adipiscing elit, sed diam nonummy nibh euismod tincidunt ut laoreet dolore magna aliquam erat volutpat. Ut wisi enim ad minim veniam, quis nostrud exerci tation ullamcorper suscipit lobortis nisl ut aliquip ex ea commodo consequat. Duis autem vel eum iriure dolor in hendrerit in vulputate velit esse molestie consequat,Lorem ipsum dolor sit amet, cons ectetuer adipiscing elit, sed diam nonummy nibh euismod tincidunt ut laoreet dolore magna aliquam erat volutpat. Duis autem vel eum iriure dolor in hendrerit in vulputate velit esse molestie consequat,Lorem ipsum dolor sit amet, cons ectetuer adipiscing elit, sed diam nonummy nibh euismod tincidunt ut laoreet dolore magna aliquam erat volutpat.</p>

  <div class="sign-off">
    <p class="name">John Doe</p>
    <p class="role">Office Maneger</p>
  </div>
  <div class="signature" role="img" aria-label="Handwritten signature"></div>

  <div class="rule"></div>

  <footer class="contact-bar">
    <div class="contact-item phone">
      <svg width="24" height="24" viewBox="0 0 24 24"><path d="M6.6 10.8c1.4 2.8 3.8 5.1 6.6 6.6l2.2-2.2c.3-.3.7-.4 1-.2 1.1.4 2.3.6 3.6.6.6 0 1 .4 1 1V20c0 .6-.4 1-1 1C10.6 21 3 13.4 3 4c0-.6.4-1 1-1h3.5c.6 0 1 .4 1 1 0 1.3.2 2.5.6 3.6.1.3 0 .7-.2 1l-2.3 2.2z"/></svg>
      <span>(000) 000 0000</span>
    </div>
    <div class="contact-item email">
      <svg width="24" height="18" viewBox="0 0 24 18"><path d="M0 0h24v18H0z M1.5 1.5l10.5 9 10.5-9" fill="var(--brand-blue-light)"/><path d="M1 1l11 9 11-9" fill="none" stroke="var(--footer)" stroke-width="1.6"/><path d="M1 17l8-7M23 17l-8-7" fill="none" stroke="var(--footer)" stroke-width="1.4"/></svg>
      <span>email@company.com</span>
    </div>
    <div class="contact-item address">
      <svg width="22" height="32" viewBox="0 0 22 32"><path d="M11 0C4.9 0 0 4.9 0 11c0 8 11 21 11 21s11-13 11-21C22 4.9 17.1 0 11 0zm0 16a5 5 0 1 1 0-10 5 5 0 0 1 0 10z"/></svg>
      <span>4187 Marlowe Ct. Apex<br>North Carolina 27614</span>
    </div>
  </footer>
</main>
</body>
</html>
```